Postcard design to acquire new clients for my Property Management Company

I'm looking for a postcard design that I can send to prospective clients detailing information about my company and services.
Postcard should be eye catching and contain information from www.bramblecrestpm.com. I've provided a few screen shots for the most important information and my logo.
Target Market(s)
Real Estate
Industry/Entity Type
Real Estate
Font styles to use
Sans Serif
Requirements
Must have
- Must be eye catching!! this will be a direct mail piece - I'd like for the card to be read and not tossed in the trash immediately.
Design que from the logo.
A place to write / print the receipts name and address.
our physical address - 2387 Hollow Pine Road, Lubbock, TX 79852.
Should not have
- the contact information on the business card is not accurate - please use info from website.

```html
<!DOCTYPE html>
<html lang="en">
<head>
<meta charset="utf-8">
<title>Bramblecrest Property Management Postcard</title>
<link href="https://fonts.googleapis.com/css2?family=Montserrat:wght@400;500;600;700;800&display=swap" rel="stylesheet">
<style>
:root{
  --stage:#262626;
  --brand-blue:#0f4d8a;
  --slate:#3f4857;
  --panel-gray:#a4a4a4;
  --ink:#0b0b0b;
  --soft-ink:#444;
  --white:#ffffff;
}
*{margin:0;padding:0;box-sizing:border-box}
html,body{width:1200px;height:723px;overflow:hidden;background:var(--stage);font-family:'Montserrat',sans-serif}
.card{position:absolute;top:176px;width:560px;height:370px;overflow:hidden;background:var(--white);box-shadow:0 10px 24px rgba(0,0,0,.55)}
.card-front{left:25px}
.card-back{left:615px}
.card svg.shapes{position:absolute;inset:0}
.t{position:absolute;white-space:nowrap}
/* front */
.brand-name{right:14px;top:8px;font-size:22px;font-weight:700;letter-spacing:5px;color:var(--brand-blue)}
.brand-sub{right:14px;top:37px;font-size:11.5px;font-weight:500;letter-spacing:3.6px;color:var(--brand-blue)}
.headline-1{right:13px;top:86px;font-size:48px;font-weight:800;color:var(--ink);letter-spacing:-1px}
.headline-2{right:13px;top:134px;font-size:33px;font-weight:700;color:var(--brand-blue);letter-spacing:-.5px}
.headline-3{right:14px;top:171px;font-size:26px;font-weight:700;color:var(--ink);letter-spacing:-.5px}
.tagline{right:14px;top:213px;font-size:12.6px;line-height:15.5px;color:var(--soft-ink);text-align:right}
.contact-label{left:231px;top:293px;font-size:14px;font-weight:800;color:var(--ink)}
.contact-line{font-size:14px;color:var(--white);font-weight:500}
/* back */
.services-title{left:0;width:285px;top:11px;text-align:center;font-size:15px;font-weight:800;color:var(--white);letter-spacing:.3px}
.service-name{font-size:11.8px;font-weight:600;color:var(--brand-blue)}
.service-copy{font-size:7.3px;line-height:7.8px;color:var(--ink);font-weight:500;letter-spacing:-.1px}
.dollar-icon{left:12px;top:150px;font-size:22px;font-weight:700;color:var(--brand-blue)}
.cta{color:var(--white);font-size:17.5px;font-weight:700;letter-spacing:.3px}
.office-address{left:8px;top:351px;font-size:9.5px;font-weight:500;color:var(--white);letter-spacing:.2px}
</style>
</head>
<body>

<section class="card card-front" aria-label="Postcard front">
  <svg class="shapes" width="560" height="370" viewBox="0 0 560 370">
    <defs>
      <linearGradient id="streetTones" x1="0" y1="0" x2="0" y2="1">
        <stop offset="0" stop-color="#dfe4ea"/>
        <stop offset=".55" stop-color="#c9ced3"/>
        <stop offset=".75" stop-color="#8c939a"/>
        <stop offset="1" stop-color="#5d6670"/>
      </linearGradient>
    </defs>
    <rect width="560" height="370" fill="var(--slate)"/>
    <polygon points="0,0 126,0 104,38 0,38" fill="var(--brand-blue)"/>
    <polygon points="265,0 560,0 560,310 230,310 305,183" fill="var(--white)"/>
    <polygon points="0,37 210,37 295,183 210,332 0,332" fill="url(#streetTones)" role="img" aria-label="Photo of white suburban houses along a street with a parked car"/>
    <polygon points="333,297 560,297 560,310 326,310" fill="var(--panel-gray)"/>
    <polygon points="228,310 560,310 560,370 265,370" fill="var(--brand-blue)"/>
    <rect x="508" y="205" width="52" height="2" fill="var(--brand-blue)"/>
  </svg>
  <div class="t brand-name">BRAMBLECREST</div>
  <div class="t brand-sub">PROPERTY MANAGEMENT</div>
  <div class="t headline-1">PROPERTY</div>
  <div class="t headline-2">MANAGEMENT</div>
  <div class="t headline-3">ACROSS LUBBOCK</div>
  <div class="t tagline">Maximize your financial returns with<br>support from our rental specialists</div>
  <div class="t contact-label">Contact us;</div>
  <div class="t contact-line" style="left:246px;top:307px">Call: (806) 555-0147</div>
  <div class="t contact-line" style="left:258px;top:324px">Email: info@bramblecrestpm.com</div>
  <div class="t contact-line" style="left:268px;top:341px">Web: bramblecrestpm.com</div>
</section>

<section class="card card-back" aria-label="Postcard back">
  <svg class="shapes" width="560" height="370" viewBox="0 0 560 370">
    <rect x="0" y="0" width="333" height="288" fill="var(--panel-gray)"/>
    <polygon points="0,9 270,9 285,32 0,32" fill="var(--brand-blue)"/>
    <polygon points="0,288 457,288 498,370 0,370" fill="var(--brand-blue)"/>
    <rect x="468" y="10" width="78" height="85" fill="none" stroke="var(--brand-blue)" stroke-width="1.5"/>
    <g stroke="var(--ink)" stroke-width="1">
      <line x1="352" y1="137" x2="545" y2="137"/>
      <line x1="352" y1="187" x2="545" y2="187"/>
      <line x1="352" y1="247" x2="545" y2="247"/>
    </g>
    <g fill="var(--brand-blue)" stroke="var(--brand-blue)">
      <path d="M8 56 L20 45 L32 56 L29 56 L29 64 L11 64 L11 56 Z" stroke="none"/>
      <rect x="17" y="58" width="6" height="6" fill="var(--panel-gray)" stroke="none"/>
      <circle cx="14" cy="101" r="4" stroke="none"/><circle cx="26" cy="101" r="4" stroke="none"/>
      <path d="M7 114 Q7 106 14 106 Q21 106 21 114 Z M19 114 Q19 106 26 106 Q33 106 33 114 Z" stroke="none"/>
      <path d="M10 244 L24 230" stroke-width="3.2" fill="none"/>
      <path d="M18 226 L27 221 L33 230 L29 232 L25 228 L23 233 Z" stroke="none"/>
      <circle cx="173" cy="52" r="7" fill="none" stroke-width="2.6"/>
      <line x1="178" y1="57" x2="184" y2="63" stroke-width="3"/>
      <path d="M164 88 L164 103 L185 103" fill="none" stroke-width="1.4"/>
      <g stroke="none"><rect x="168" y="96" width="2" height="5"/><rect x="172" y="92" width="2" height="9"/><rect x="176" y="95" width="2" height="6"/><rect x="180" y="90" width="2" height="11"/></g>
      <path d="M174 154 L184 157 Q184 170 174 176 Q164 170 164 157 Z" stroke="none"/>
      <path d="M174 157 L181 159 Q181 168 174 173 Z" fill="var(--panel-gray)" stroke="none"/>
      <g fill="none" stroke-width="1.4">
        <line x1="174" y1="217" x2="174" y2="233"/><line x1="164" y1="220" x2="184" y2="220"/><line x1="168" y1="233" x2="180" y2="233"/>
        <path d="M164 220 L160 228 L168 228 Z M184 220 L180 228 L188 228 Z"/>
      </g>
    </g>
  </svg>
  <div class="t services-title">OUR SERVICES</div>
  <div class="t dollar-icon">$</div>

  <div class="t service-name" style="left:38px;top:48px">Property Marketing</div>
  <div class="t service-copy" style="left:38px;top:64px">Let us take over your marketing<br>for you and we'll find a quali-<br>fied renter quickly.</div>

  <div class="t service-name" style="left:39px;top:101px">Tenant Screening</div>
  <div class="t service-copy" style="left:39px;top:117px">We don't just find someone to<br>rent your home—we find the<br>best renters. We screen all ap-<br>plications using fair housing<br>guidelines to protect you.</div>

  <div class="t service-name" style="left:38px;top:161px">Rent Collection</div>
  <div class="t service-copy" style="left:39px;top:178px">Stop guessing when you'll re-<br>ceive your rental earnings every<br>month and say hello to consis-<br>tent payments. We keep your<br>tenants current.</div>

  <div class="t service-name" style="left:38px;top:224px">Maintenance</div>
  <div class="t service-copy" style="left:39px;top:241px">Still scrambling to respond to<br>repair requests every time you<br>receive a tenant call? Let us co-<br>ordinate repair work on your<br>behalf!</div>

  <div class="t service-name" style="left:193px;top:46px">Property Inspections</div>
  <div class="t service-copy" style="left:193px;top:62px">We visit every home in our<br>portfolio regularly.</div>

  <div class="t service-name" style="left:193px;top:91px">Financial Reporting</div>
  <div class="t service-copy" style="left:193px;top:108px">Keep a handle on your real<br>estate performance. We generate<br>monthly statements so you can<br>review income &amp; expenses at a<br>moment's notice.</div>

  <div class="t service-name" style="left:193px;top:156px">Evictions</div>
  <div class="t service-copy" style="left:193px;top:173px">When things go wrong inside<br>your rental home, rest easy with<br>the experts on your side. We will<br>handle evictions for you &amp; find<br>new renters when its over.</div>

  <div class="t service-name" style="left:193px;top:221px">Legal Guidance</div>
  <div class="t service-copy" style="left:193px;top:238px">Don't accidentally violate one of<br>the many ordinances and hous-<br>ing laws governing your relation-<br>ship with your tenants. Let us<br>keep you compliant.</div>

  <div class="t cta" style="left:76px;top:305px">CHOOSE THE RIGHT</div>
  <div class="t cta" style="left:7px;top:326px">PROPERTY MANAGEMENT SYSTEM</div>
  <div class="t office-address">2387 Hollow Pine Road, Lubbock, TX 79852</div>
</section>

</body>
</html>
```